Caldrift - Where every box finds its place!

Hello,
I'd like to update, re-vamp, and re-tool this current power point presentation with slightly more professional appearance as well as more accurately reflect the website -caldrift.com- color scheme and sleek design scheme. Please see attached.
We at Caldrift pride ourselves on seeking to rework an archaic business into something progressive, cost effective, more reliable, and easily accessible in todays fast growing market that has only gotten more expensive, more costly and less indirect over the last couple years.

Target Market(s)

New updated and hassle free moving opportunities no matter how large or how small in a market that begs for a change

Industry/Entity Type

Logistics/Moving

Requirements
Must have
• The current color scheme from the -caldrift.com- website as well as the inclusion of the current data on the sample power point presentation provided but with updated graphics

```html
<!DOCTYPE html>
<html lang="en">
<head>
<meta charset="utf-8">
<title>Caldrift – Pitch Deck</title>
<link href="https://fonts.googleapis.com/css2?family=Poppins:wght@400;500;600;700;800&display=swap" rel="stylesheet">
<style>
:root{
  --blue:#1f63d6;
  --blue-dark:#1750b4;
  --yellow:#fcc419;
  --ink:#2b2f3a;
  --muted:#5b6170;
  --white:#ffffff;
  --canvas:#d9dce3;
  --photo-a:#c9b9a8;
  --photo-b:#8f7d6b;
}
*{box-sizing:border-box;margin:0;padding:0}
html,body{width:1200px;height:4040px;overflow:hidden}
body{background:var(--canvas);font-family:'Poppins',sans-serif;color:var(--ink);padding:10px 8px}
.slide{position:relative;width:1184px;height:660px;margin-bottom:12px;overflow:hidden;background:var(--white)}
.slide:last-child{margin-bottom:0}
.brand{display:flex;align-items:center;gap:12px;font-weight:700;color:var(--blue)}
.brand .mark{width:22px;height:22px;background:var(--yellow)}
.brand-footer{position:absolute;right:40px;bottom:26px;font-size:24px}
.page-no{position:absolute;left:0;bottom:0;width:48px;height:40px;display:flex;align-items:center;justify-content:center;color:var(--white);font-weight:700;font-size:20px;background:var(--blue)}
.page-no.yellow{background:var(--yellow);color:var(--ink)}
.photo{position:absolute}

/* Cover */
.cover{background:var(--blue)}
.cover .brand{position:absolute;left:80px;top:170px;color:var(--white);flex-direction:column;align-items:flex-start;gap:18px;font-size:56px}
.cover .brand .mark{width:64px;height:64px}
.cover h1{position:absolute;left:80px;top:350px;width:560px;font-size:44px;line-height:1.2;font-weight:700;color:var(--white);text-transform:uppercase}
.cover .strips{position:absolute;right:0;top:0}

/* About */
.about .brand{position:absolute;left:70px;top:50px;font-size:32px}
.about h2{position:absolute;left:70px;top:140px;font-size:40px;font-weight:800;color:var(--blue)}
.about h2 span,.vision h2 span{color:var(--yellow)}
.about .copy{position:absolute;left:70px;top:215px;width:560px;font-size:15px;line-height:1.55;color:var(--muted)}
.about .copy p{margin-bottom:18px}
.about .yellow-block{position:absolute;right:0;top:0;width:430px;height:660px;background:var(--yellow)}

/* Vision */
.vision{background:#f6f7fa}
.vision h2{position:absolute;left:0;right:0;top:40px;text-align:center;font-size:36px;font-weight:800;color:var(--blue)}
.vision .lead{position:absolute;left:0;right:0;top:95px;text-align:center;font-size:15px;color:var(--muted)}
.cards{position:absolute;left:70px;top:140px;display:flex;gap:36px}
.card{width:324px;height:400px;padding:30px 26px;text-align:center;color:var(--white);background:var(--blue)}
.card.alt{background:var(--yellow);color:var(--ink)}
.card .icon{width:80px;height:80px;margin:0 auto 22px;border-radius:50%;background:var(--white);display:flex;align-items:center;justify-content:center}
.card h3{font-size:26px;font-weight:700;margin-bottom:8px}
.card .key{font-size:16px;font-weight:600;line-height:1.35;margin-bottom:12px}
.card .body{font-size:13px;line-height:1.5;opacity:.92}

/* Problems */
.problems{background:linear-gradient(160deg,var(--blue) 0%,var(--blue-dark) 100%)}
.problems h2{position:absolute;left:0;right:0;top:42px;text-align:center;font-size:36px;font-weight:800;color:var(--white)}
.problems .rail{position:absolute;left:120px;right:120px;top:172px;height:3px;background:var(--white);opacity:.7}
.issues{position:absolute;left:90px;top:150px;display:flex;gap:36px}
.issue{position:relative;width:224px;height:350px;border-radius:22px;background:var(--yellow);padding:70px 22px 0;text-align:center}
.issue .num{position:absolute;left:87px;top:-26px;width:50px;height:50px;border-radius:50%;background:var(--white);border:4px solid var(--yellow);display:flex;align-items:center;justify-content:center;font-weight:700;font-size:20px;color:var(--blue)}
.issue h3{font-size:21px;font-weight:700;color:var(--ink);margin-bottom:10px}
.issue p{font-size:13px;line-height:1.5;color:var(--ink)}
.issue .badge{position:absolute;left:72px;bottom:-40px;width:80px;height:80px;border-radius:50%;background:var(--white);display:flex;align-items:center;justify-content:center;box-shadow:0 4px 12px rgba(0,0,0,.15)}
.problems .brand-footer{color:var(--white)}

/* Solution */
.solution .circle-yellow{position:absolute;left:-60px;top:80px;width:470px;height:470px;border-radius:50%;background:var(--yellow)}
.solution .value{position:absolute;left:350px;top:90px;width:120px;height:120px;border-radius:50%;background:var(--yellow);display:flex;align-items:center;justify-content:center;text-align:center;font-size:17px;font-weight:700;color:var(--ink);border:5px solid var(--white)}
.solution .promise{position:absolute;left:40px;top:420px;width:170px;height:170px;border-radius:50%;background:var(--blue);color:var(--white);display:flex;align-items:center;justify-content:center;text-align:center;font-size:14px;font-weight:600;line-height:1.35;padding:18px;border:5px solid var(--white)}
.solution h2{position:absolute;left:540px;top:50px;font-size:32px;font-weight:800;color:var(--ink)}
.steps{position:absolute;left:540px;top:110px;width:600px;list-style:none}
.steps li{display:flex;gap:18px;margin-bottom:18px}
.steps .dot{flex:none;width:44px;height:44px;border-radius:50%;background:var(--blue);display:flex;align-items:center;justify-content:center}
.steps h3{font-size:17px;font-weight:600;color:var(--ink)}
.steps p{font-size:12.5px;line-height:1.45;color:var(--muted)}

/* Thanks */
.thanks{background:var(--yellow)}
.thanks .brand{position:absolute;left:70px;top:390px;color:var(--white);font-size:52px}
.thanks .brand .mark{background:var(--white);width:40px;height:40px}
.thanks h2{position:absolute;left:70px;top:470px;font-size:82px;line-height:1.1;font-weight:700;color:var(--white)}
.contacts{position:absolute;left:690px;top:270px;list-style:none}
.contacts li{display:flex;align-items:center;gap:26px;margin-bottom:36px;color:var(--white);font-size:22px;font-weight:500;line-height:1.35}
.contacts .dot{flex:none;width:62px;height:62px;border-radius:50%;background:var(--blue);display:flex;align-items:center;justify-content:center}
</style>
</head>
<body>

<section class="slide cover">
  <div class="brand"><span class="mark"></span>Caldrift</div>
  <h1>Moving for the next generation</h1>
  <svg class="strips" width="600" height="660" viewBox="0 0 600 660" role="img" aria-label="Angled photo panels of a warehouse and a smiling mover in a safety vest">
    <defs>
      <linearGradient id="wh" x1="0" y1="0" x2="0" y2="1"><stop offset="0" stop-color="#e4e8ef"/><stop offset="1" stop-color="#9aa6b8"/></linearGradient>
      <linearGradient id="mv" x1="0" y1="0" x2="1" y2="1"><stop offset="0" stop-color="#d8c7a8"/><stop offset="1" stop-color="#c6b54a"/></linearGradient>
    </defs>
    <polygon points="70,0 170,0 110,420 10,420" fill="url(#wh)"/>
    <polygon points="220,0 310,0 250,420 160,420" fill="url(#wh)"/>
    <polygon points="360,0 600,0 600,560 300,560" fill="url(#mv)"/>
  </svg>
</section>

<section class="slide about">
  <div class="brand"><span class="mark"></span>Caldrift</div>
  <h2>ABOUT <span>US</span></h2>
  <div class="copy">
    <p>Caldrift is the next logical evolution in professional moving. Professional moving clients have battled soaring prices, acute capacity problems and deteriorating service levels.</p>
    <p>Caldrift was founded by lifelong moving professionals who have developed the answer to better moving services. Poised as the industry disruptor, we deliver faster, offer guaranteed prices and even offer no-credit check financing options.</p>
    <p>We are a technology first organization using proprietary software to deliver moving's best service experience.</p>
  </div>
  <div class="yellow-block"></div>
  <div class="photo" role="img" aria-label="Photo of a woman smiling as she unpacks a cardboard box on a sofa" style="left:690px;top:60px;width:430px;height:370px;background:linear-gradient(135deg,#ece6df,var(--photo-a) 60%,var(--photo-b))"></div>
  <div class="page-no">2</div>
</section>

<section class="slide vision">
  <h2>CALDRIFT <span>VISION</span></h2>
  <p class="lead">The traditional moving industry is broken, outdated, inefficient, and unable to change</p>
  <div class="cards">
    <div class="card">
      <div class="icon"><svg width="40" height="40" viewBox="0 0 40 40" fill="none" stroke="#1f63d6" stroke-width="3"><circle cx="20" cy="20" r="16"/><circle cx="20" cy="20" r="9"/><circle cx="20" cy="20" r="2" fill="#1f63d6"/></svg></div>
      <h3>Our Vision</h3>
      <p class="key">Revolutionize an $18B industry by providing great value to everyone involved</p>
      <p class="body">Caldrift Customers, Consumers, Movers, Corporate Clients, and Relocation Management Companies. All receive better value with Caldrift than anywhere else.</p>
    </div>
    <div class="card alt">
      <div class="icon"><svg width="40" height="40" viewBox="0 0 40 40" fill="none" stroke="#1f63d6" stroke-width="3"><path d="M3 20 Q20 4 37 20 Q20 36 3 20Z"/><circle cx="20" cy="20" r="6"/></svg></div>
      <h3>Our Mission</h3>
      <p class="key">Disrupt a sleepy giant of an inefficient industry</p>
      <p class="body">Caldrift's deep understanding of the professional moving industry, supported by extensive market research, has set Caldrift up for ultimate success in disrupting this industry by creating cost-saving efficiencies throughout.</p>
    </div>
    <div class="card">
      <div class="icon"><svg width="40" height="40" viewBox="0 0 40 40" fill="none" stroke="#1f63d6" stroke-width="3"><path d="M8 36V5"/><path d="M8 6h24l-5 7 5 7H8"/></svg></div>
      <h3>Our Goal</h3>
      <p class="key">Becoming the moving platform of choice</p>
      <p class="body">As Caldrift's market share grows, the customer acquisition cost and operational cost plummets. This creates even more market penetration, more efficiencies, and exponential growth.</p>
    </div>
  </div>
  <div class="page-no yellow">3</div>
  <div class="brand brand-footer"><span class="mark"></span>Caldrift</div>
</section>

<section class="slide problems">
  <h2>MOVING'S PROBLEMS</h2>
  <div class="rail"></div>
  <div class="issues">
    <div class="issue">
      <div class="num">1</div>
      <h3>COST</h3>
      <p>Moving cost has skyrocketed over the last three years. Charges have increased 38% since 2018.</p>
      <div class="badge"><svg width="38" height="38" viewBox="0 0 38 38" fill="none" stroke="#1f63d6" stroke-width="3"><circle cx="19" cy="19" r="15"/><path d="M24 13h-7a3 3 0 0 0 0 6h4a3 3 0 0 1 0 6h-7M19 9v4M19 25v4"/></svg></div>
    </div>
    <div class="issue">
      <div class="num">2</div>
      <h3>CAPACITY</h3>
      <p>Long-haul driver shortages and limited equipment coupled with growing demand has pushed capacity to a crisis state.</p>
      <div class="badge"><svg width="40" height="38" viewBox="0 0 40 38" fill="none" stroke="#1f63d6" stroke-width="3"><rect x="3" y="10" width="22" height="16"/><path d="M25 15h7l5 6v5H25"/><circle cx="11" cy="29" r="3"/><circle cx="31" cy="29" r="3"/></svg></div>
    </div>
    <div class="issue">
      <div class="num">3</div>
      <h3>SERVICE</h3>
      <p>Quality labor has been difficult to source and afford. Initially as Meridian Research reports a decline in service quality.</p>
      <div class="badge"><svg width="38" height="38" viewBox="0 0 38 38" fill="none" stroke="#1f63d6" stroke-width="3"><circle cx="19" cy="13" r="7"/><path d="M6 34c1-8 6-12 13-12s12 4 13 12"/></svg></div>
    </div>
    <div class="issue">
      <div class="num">4</div>
      <h3>TRANSPARENCY</h3>
      <p>Moving cost has skyrocketed over the last three years. Charges have increased 38% since 2018.</p>
      <div class="badge"><svg width="38" height="38" viewBox="0 0 38 38" fill="none" stroke="#1f63d6" stroke-width="3"><rect x="6" y="4" width="26" height="30" rx="2"/><path d="M11 12h16M11 19h16M11 26h10"/></svg></div>
    </div>
  </div>
  <div class="page-no yellow">4</div>
  <div class="brand brand-footer"><span class="mark"></span>Caldrift</div>
</section>

<section class="slide solution">
  <div class="circle-yellow"></div>
  <div class="photo" role="img" aria-label="Circular photo of hands taping a moving box" style="left:-20px;top:120px;width:390px;height:390px;border-radius:50%;background:linear-gradient(135deg,#e3d6c6,var(--photo-a) 55%,var(--photo-b))"></div>
  <div class="value">Value Proposition</div>
  <div class="promise">Bringing the Customer Experience to the 21st Century</div>
  <h2>SOLUTION</h2>
  <ul class="steps">
    <li><span class="dot"><svg width="22" height="22" viewBox="0 0 22 22" fill="none" stroke="#fff" stroke-width="2.5"><path d="M4 11l5 5 9-10"/></svg></span><div><h3>On-Demand Process</h3><p>Caldrift automatically matches customers, movers, carriers and storage through one simple booking platform.</p></div></li>
    <li><span class="dot"><svg width="22" height="22" viewBox="0 0 22 22" fill="none" stroke="#fff" stroke-width="2.5"><circle cx="11" cy="8" r="4"/><path d="M3 20c1-5 4-7 8-7s7 2 8 7"/></svg></span><div><h3>One Point of Contact</h3><p>Today moves are sold from broker to broker. With Caldrift, one contact sees every move from start to finish.</p></div></li>
    <li><span class="dot"><svg width="22" height="22" viewBox="0 0 22 22" fill="none" stroke="#fff" stroke-width="2.5"><rect x="2" y="5" width="18" height="13" rx="2"/><path d="M2 10h18"/></svg></span><div><h3>Book Now Pay Later</h3><p>Moving has a high price tag, but no one has ever offered a pay-later solution. Move now and settle later.</p></div></li>
    <li><span class="dot"><svg width="22" height="22" viewBox="0 0 22 22" fill="none" stroke="#fff" stroke-width="2.5"><path d="M11 20s-7-6-7-11a7 7 0 0 1 14 0c0 5-7 11-7 11z"/><circle cx="11" cy="9" r="2.5"/></svg></span><div><h3>GPS Tracking</h3><p>Anyone can confidently see where their shipment is at any time with live tracking of every truck on the road.</p></div></li>
    <li><span class="dot"><svg width="22" height="22" viewBox="0 0 22 22" fill="none" stroke="#fff" stroke-width="2.5"><path d="M3 12l8-9h8v8l-9 8z"/><circle cx="15" cy="7" r="1.5"/></svg></span><div><h3>Simple Honest Pricing</h3><p>Caldrift's proprietary algorithms set fair and clear prices, so customers pay the price they were quoted.</p></div></li>
  </ul>
  <div class="page-no">5</div>
  <div class="brand brand-footer"><span class="mark"></span>Caldrift</div>
</section>

<section class="slide thanks">
  <div class="photo" role="img" aria-label="Faint warehouse photo behind a yellow wash" style="inset:0;background:linear-gradient(180deg,rgba(255,255,255,.18),rgba(200,150,0,.18))"></div>
  <div class="brand"><span class="mark"></span>Caldrift</div>
  <h2>Thank You!</h2>
  <ul class="contacts">
    <li><span class="dot"><svg width="26" height="26" viewBox="0 0 22 22" fill="none" stroke="#fff" stroke-width="2.5"><path d="M11 20s-7-6-7-11a7 7 0 0 1 14 0c0 5-7 11-7 11z"/><circle cx="11" cy="9" r="2.5"/></svg></span><span>482 Harbor Lane<br>Riverton, CO 80412</span></li>
    <li><span class="dot"><svg width="26" height="26" viewBox="0 0 24 24" fill="#fff"><path d="M6.6 10.8a15 15 0 0 0 6.6 6.6l2.2-2.2a1 1 0 0 1 1-.25 11.4 11.4 0 0 0 3.6.57 1 1 0 0 1 1 1V20a1 1 0 0 1-1 1A17 17 0 0 1 3 4a1 1 0 0 1 1-1h3.5a1 1 0 0 1 1 1c0 1.25.2 2.45.57 3.57a1 1 0 0 1-.25 1z"/></svg></span><span>(800) 555-0142</span></li>
    <li><span class="dot"><svg width="26" height="26" viewBox="0 0 24 24" fill="none" stroke="#fff" stroke-width="2.2"><circle cx="12" cy="12" r="9"/><path d="M3 12h18M12 3c3 3 3 15 0 18M12 3c-3 3-3 15 0 18"/></svg></span><span>caldrift.com<br>support@caldrift.com</span></li>
  </ul>
</section>

</body>
</html>
```